Volbrey Inc Business Card

Looking to get an updated business card for a Contract Machining company (www.volbreyinc.example) - looking for a clean design the portrays the technical nature of the business - colors can follow the website design and be in any combination that makes sense (red black, white, metallic or silver) - logos attached for use also. Would like space for: Name, title, business phone (555 214-3086), cell phone , website (www.volbreyinc.example) - possibly QR code could be integrated for website (designer choice), business address - 418 Harlow Bend, Brennick, OH 48199 (cards will be for 4 employees, I will either need to modify a template or I can provide individual information)
Target Market(s)
Aerospace, defense and medical device manufacturing companies that need machining
Industry/Entity Type
Machining for aerospace, defense, medical
Contact Information for Business Card
Name, Title, Business Phone, Cell Phone, email, business website and business address
Look and feel

```html
<!DOCTYPE html>
<html lang="en">
<head>
<meta charset="utf-8">
<title>Volbrey Inc Business Card</title>
<link href="https://fonts.googleapis.com/css2?family=Montserrat:wght@400;500;700;800&display=swap" rel="stylesheet">
<style>
  :root {
    --backdrop: #1b1b1b;
    --card: #262626;
    --card-edge: #2e2e2e;
    --red: #b8202a;
    --white: #f2f2f2;
    --emboss: #3a3a3a;
    --emboss-light: #4a4a4a;
  }
  * { margin: 0; padding: 0; box-sizing: border-box; }
  html, body {
    width: 1200px; height: 900px; overflow: hidden;
    background: var(--backdrop);
    font-family: "Montserrat", sans-serif;
  }
  .stage {
    width: 1200px; height: 900px;
    display: flex; flex-direction: column; align-items: center; justify-content: center;
    gap: 40px;
  }
  .card {
    width: 700px; height: 400px;
    background: linear-gradient(135deg, var(--card-edge), var(--card));
    box-shadow: 0 10px 30px rgba(0,0,0,.5);
    position: relative;
  }
  /* front */
  .card--front { display: flex; flex-direction: column; align-items: center; justify-content: center; gap: 22px; }
  .front-disc {
    width: 150px; height: 150px; border-radius: 50%;
    background: radial-gradient(circle at 35% 30%, var(--emboss-light), var(--emboss));
    box-shadow: 0 2px 4px rgba(0,0,0,.5);
  }
  .front-name {
    font-weight: 800; font-size: 34px; letter-spacing: 2px;
    color: var(--emboss-light); text-transform: uppercase;
  }
  /* back */
  .card--back { display: flex; align-items: center; padding: 0 40px 0 50px; }
  .brand {
    flex: none; width: 300px;
    font-weight: 800; font-size: 38px; line-height: 1;
    color: var(--red); text-transform: uppercase; white-space: nowrap;
  }
  .divider { flex: none; width: 2px; height: 200px; background: var(--red); margin: 0 26px 0 16px; }
  .contact { color: var(--white); font-size: 17px; line-height: 1.35; }
  .contact__name { color: var(--red); font-weight: 700; font-size: 23px; text-transform: uppercase; letter-spacing: .5px; line-height: 1.1; }
  .contact__title { text-transform: uppercase; font-size: 16px; margin-bottom: 10px; }
  .contact__address { margin-bottom: 6px; }
  .contact__line { display: flex; align-items: center; gap: 8px; }
  .contact__line svg { width: 12px; height: 12px; flex: none; }
</style>
</head>
<body>
<main class="stage">
  <section class="card card--front">
    <div class="front-disc"></div>
    <div class="front-name">Volbrey Inc.</div>
  </section>

  <section class="card card--back">
    <div class="brand">Volbrey Inc.</div>
    <div class="divider"></div>
    <div class="contact">
      <div class="contact__name">Dorian Pell</div>
      <div class="contact__title">Director</div>
      <div class="contact__address">418 Harlow Bend,<br>Brennick, OH 48199</div>
      <div class="contact__line">
        <svg viewBox="0 0 12 12"><path d="M3 1l2 2-1 1.5c.6 1.4 1.6 2.4 3 3L8.5 6.5l2 2-1.5 2C5 10 2 7 1.5 2.5z" fill="var(--red)"/></svg>
        <span>555 214-3086</span>
      </div>
      <div class="contact__line">
        <svg viewBox="0 0 12 12"><rect x="3" y="1" width="6" height="10" rx="1" fill="none" stroke="var(--red)" stroke-width="1.3"/></svg>
        <span>555-214-7719</span>
      </div>
      <div class="contact__line">
        <svg viewBox="0 0 12 12"><rect x="1" y="2.5" width="10" height="7" fill="none" stroke="var(--red)" stroke-width="1.2"/><path d="M1 2.5l5 4 5-4" fill="none" stroke="var(--red)" stroke-width="1.2"/></svg>
        <span>info@volbreyinc.example</span>
      </div>
      <div class="contact__line">
        <svg viewBox="0 0 12 12"><circle cx="6" cy="6" r="4.8" fill="none" stroke="var(--red)" stroke-width="1.2"/><path d="M1.2 6h9.6M6 1.2c-2.4 3-2.4 6.6 0 9.6M6 1.2c2.4 3 2.4 6.6 0 9.6" fill="none" stroke="var(--red)" stroke-width="1"/></svg>
        <span>www.volbreyinc.example</span>
      </div>
    </div>
  </section>
</main>
</body>
</html>
```